Pagina Lartovira

The Lartovira is a company dealing with leasing and selling real estate. The current site can be accessed at www.lartovira-exemplo.com.br. We intend to redesign the look of the site and for that we would like to redesign the home page and the page with information and pictures of the property. The homepage should maintain the characteristics of the current common design simple, short and straightforward. The page with the data of the properties should be accessed with two changes page as it is currently running. The search from the map by region and should be maintained.
The page containing the information of the property will provide a total of 15 small pictures that when clicked will appear in larger size. The colors to be used should be orange, blue, black and white. The map can be maintained in the current colors.
Updates

Payment guaranteed. Deadline for submission of designs April 27.

Industry/Entity Type

Real Estate

Requirements
Must have
• Search by map regions and search box
address
keep colors from the current page
phones
clean look
Nice to have
• clean look
Should not have
• We like the current page. We just want to make it compatible with modern and new design trends and monitors.

```html
<!DOCTYPE html>
<html lang="pt-BR">
<head>
<meta charset="utf-8">
<title>Lartovira</title>
<link rel="stylesheet" href="https://fonts.googleapis.com/css2?family=Ubuntu:wght@400;500;700&family=Open+Sans:wght@400;600&display=swap">
<style>
:root{
  --orange:#f5850a;
  --orange-dark:#e07600;
  --navy:#1f2a7a;
  --page-bg:#eef0ee;
  --panel:#ffffff;
  --footer:#2f4a73;
  --footer-deep:#233b60;
  --footer-text:#b9c6dc;
  --footer-head:#d5deeb;
  --map-sea:#5db3e8;
  --map-land:#05933a;
  --text:#1e1e1e;
  --alert-bg:#f3dede;
  --alert-text:#b1141a;
  --ribbon:#1a8fd6;
}
*{box-sizing:border-box;margin:0;padding:0}
html,body{width:1200px;height:835px;overflow:hidden}
body{position:relative;background:var(--page-bg);font-family:"Ubuntu",sans-serif;color:var(--text)}
.backdrop{position:absolute;left:0;top:0;width:1200px;height:640px;background:linear-gradient(90deg,#f2f3f1,#e9ecea 60%,#e3e8ec)}
.utility{position:absolute;left:986px;top:8px;font-size:12px;color:#666;font-family:"Open Sans",sans-serif}
.sidebar{position:absolute;left:140px;top:0;width:238px;height:560px;background:var(--orange);box-shadow:0 14px 14px -8px rgba(0,0,0,.35)}
.brand{position:absolute;left:130px;top:29px;width:258px;height:88px;background:var(--panel);box-shadow:0 2px 4px rgba(0,0,0,.2);display:flex;align-items:center;justify-content:center;gap:10px}
.brand-mark{width:14px;height:14px;background:var(--navy)}
.brand-name{font-size:28px;font-weight:500;color:var(--navy)}
.nav{position:absolute;left:158px;top:174px;list-style:none}
.nav li{color:#fff;font-size:15px;height:28.2px;text-shadow:0 1px 1px rgba(0,0,0,.25)}
.nav li::before{content:"";display:inline-block;border-left:5px solid #fff;border-top:3.5px solid transparent;border-bottom:3.5px solid transparent;margin-right:11px;vertical-align:2px}
.divider{position:absolute;left:140px;top:456px;width:238px;border-top:1px solid rgba(0,0,0,.12);border-bottom:1px solid rgba(255,255,255,.25)}
.phones{position:absolute;left:160px;top:496px;display:flex;gap:14px;color:#fff;font-weight:700;font-size:18px;line-height:22px;text-shadow:0 1px 1px rgba(0,0,0,.3)}
.search{position:absolute;left:397px;top:29px;width:665px;height:88px;background:rgba(255,255,255,.92)}
.search h2{position:absolute;left:29px;top:12px;font-size:14px;font-weight:500;color:var(--navy)}
.select{position:absolute;left:28px;top:38px;width:184px;height:26px;border:1px solid #ccc;border-radius:3px;background:#fff;font-size:12px;color:#999;padding:5px 9px}
.select::after{content:"";position:absolute;right:10px;top:10px;border-top:5px solid #555;border-left:4px solid transparent;border-right:4px solid transparent}
.check{position:absolute;top:42px;font-size:13px;color:#333;display:flex;align-items:center;gap:10px}
.box{width:15px;height:15px;border:1px solid #bbb;border-radius:3px;background:#fff}
.box.on{background:#4aa3e0;border:3px solid #d7e9f6}
.btn{position:absolute;left:507px;top:35px;width:104px;height:31px;border-radius:3px;background:linear-gradient(#ffb226,var(--orange-dark));color:#fff;font-weight:700;font-size:16px;display:flex;align-items:center;justify-content:center;gap:8px;box-shadow:0 1px 2px rgba(0,0,0,.3)}
.section-title{position:absolute;font-size:14px;font-weight:500;color:var(--navy)}
.map{position:absolute;left:397px;top:162px;width:338px;height:401px;border:2px solid #fff;background:linear-gradient(115deg,var(--map-sea) 0%,var(--map-sea) 20%,var(--map-land) 45%,var(--map-land) 62%,var(--map-sea) 85%)}
.alert{position:absolute;left:397px;top:575px;width:336px;height:50px;background:var(--alert-bg);border-radius:3px;display:flex;align-items:center;gap:16px;padding-left:12px;font-size:12px;line-height:14px;color:var(--alert-text)}
.listing{position:absolute;left:765px;width:300px;height:90px}
.photo{position:absolute;left:0;top:0;width:134px;height:90px;border:2px solid #fff;box-shadow:0 0 2px rgba(0,0,0,.3);background:linear-gradient(#9cc2e4 0%,#cfd9e0 40%,#c4a57a 70%,#7c8b5a 100%);overflow:hidden}
.photo.active{border-color:#2f4a73}
.ribbon{position:absolute;right:-18px;top:6px;width:70px;height:14px;background:var(--ribbon);transform:rotate(35deg);color:#fff;font-size:8px;text-align:center;line-height:14px}
.facts{position:absolute;left:148px;top:-4px;font-size:12.5px;line-height:16px;display:grid;grid-template-columns:49px auto}
.facts dt{font-weight:700}
.footer{position:absolute;left:0;top:640px;width:1200px;height:155px;background:var(--footer);font-family:"Open Sans",sans-serif;color:var(--footer-text);font-size:12.5px}
.footer h3{position:absolute;top:16px;font-size:13px;font-weight:600;color:var(--footer-head);font-family:"Ubuntu",sans-serif}
.footer ul{position:absolute;top:42px;list-style:none;line-height:20.7px}
.footer ul li::before{content:"";display:inline-block;border-left:3px solid var(--footer-text);border-top:3px solid transparent;border-bottom:3px solid transparent;margin-right:5px;vertical-align:1px}
.footer .vline{position:absolute;left:598px;top:26px;width:1px;height:110px;background:rgba(255,255,255,.12)}
.address{position:absolute;left:621px;top:42px;line-height:21px}
.address strong{font-size:14px;font-weight:600;color:var(--footer-head)}
.details{position:absolute;left:841px;top:40px;display:grid;grid-template-columns:67px auto;line-height:20.7px;font-size:12px}
.details a{color:var(--footer-text)}
.copyright{position:absolute;left:0;top:795px;width:1200px;height:40px;background:var(--footer-deep);color:#8fa0bc;font-family:"Open Sans",sans-serif;font-size:11.5px;text-align:center;line-height:40px}
</style>
</head>
<body>
<div class="backdrop"></div>
<div class="utility">Login &nbsp;|&nbsp; Help</div>

<aside class="sidebar"></aside>
<div class="brand"><span class="brand-mark"></span><span class="brand-name">Lartovira</span></div>
<ul class="nav">
  <li>A empresa</li><li>Localizacao</li><li>Area Restrita</li><li>Fale Conosco</li>
  <li>Cadastre seu imovel</li><li>Informacoes ao Proprietario</li><li>Informacoes ao Locatario</li><li>Solicite seu imovel</li>
</ul>
<div class="divider"></div>
<div class="phones">
  <svg width="38" height="36" viewBox="0 0 38 36" aria-hidden="true"><path d="M2 10c0-5 8-8 17-8s17 3 17 8v3h-8v-4c-3-1-6-1-9-1s-6 0-9 1v4H2z" fill="#fff"/><g fill="#fff"><circle cx="13" cy="20" r="2.4"/><circle cx="19" cy="20" r="2.4"/><circle cx="25" cy="20" r="2.4"/><circle cx="13" cy="26" r="2.4"/><circle cx="19" cy="26" r="2.4"/><circle cx="25" cy="26" r="2.4"/><circle cx="13" cy="32" r="2.4"/><circle cx="19" cy="32" r="2.4"/><circle cx="25" cy="32" r="2.4"/></g></svg>
  <div>(48) 300 12 45<br>(48) 9100 2233</div>
</div>

<section class="search">
  <h2>Busca de imoveis</h2>
  <div class="select">Todos</div>
  <label class="check" style="left:240px"><span class="box on"></span>Para comprar</label>
  <label class="check" style="left:371px"><span class="box"></span>Para alugar</label>
  <div class="btn"><svg width="18" height="18" viewBox="0 0 18 18" aria-hidden="true"><circle cx="7" cy="7" r="5" fill="none" stroke="#fff" stroke-width="2.5"/><path d="M11 11l5 5" stroke="#fff" stroke-width="3" stroke-linecap="round"/></svg>Buscar</div>
</section>

<h2 class="section-title" style="left:426px;top:134px">Buscar imovel po regiao (location)</h2>
<div class="map" role="img" aria-label="Mapa de Florianópolis dividido nas regiões Continente, Norte, Centro, Leste e Sul"></div>
<div class="alert">
  <svg width="30" height="26" viewBox="0 0 30 26" aria-hidden="true"><path d="M15 1L29 25H1z" fill="#f2a010" stroke="#b36d00"/><rect x="13.7" y="9" width="2.6" height="9" fill="#333"/><rect x="13.7" y="20" width="2.6" height="2.6" fill="#333"/></svg>
  <p><strong>Allert!</strong> Lorem ipsum dolor sit amet, consect<br>etuer adipiscing elit.</p>
</div>

<h2 class="section-title" style="left:765px;top:134px">We Recomended</h2>
<article class="listing" style="top:164px"><div class="photo" role="img" aria-label="Foto do edifício residencial com palmeiras"><span class="ribbon">NEW</span></div>
  <dl class="facts"><dt>Bairro:</dt><dd>Coqueiros</dd><dt>Cidade:</dt><dd>CONTINENTE</dd><dt>Valor:</dt><dd>2.060,00</dd><dt>Cond.:</dt><dd>330,00</dd><dt>IPTU:</dt><dd>87,89</dd></dl></article>
<article class="listing" style="top:268px"><div class="photo active" role="img" aria-label="Foto do edifício residencial com palmeiras"></div>
  <dl class="facts"><dt>Bairro:</dt><dd>Coqueiros</dd><dt>Cidade:</dt><dd>CONTINENTE</dd><dt>Valor:</dt><dd>2.060,00</dd><dt>Cond.:</dt><dd>330,00</dd><dt>IPTU:</dt><dd>87,89</dd></dl></article>
<article class="listing" style="top:373px"><div class="photo" role="img" aria-label="Foto do edifício residencial com palmeiras"><span class="ribbon">NEW</span></div>
  <dl class="facts"><dt>Bairro:</dt><dd>Coqueiros</dd><dt>Cidade:</dt><dd>CONTINENTE</dd><dt>Valor:</dt><dd>2.060,00</dd><dt>Cond.:</dt><dd>330,00</dd><dt>IPTU:</dt><dd>87,89</dd></dl></article>
<article class="listing" style="top:477px"><div class="photo" role="img" aria-label="Foto do edifício residencial com palmeiras"></div>
  <dl class="facts"><dt>Bairro:</dt><dd>Coqueiros</dd><dt>Cidade:</dt><dd>CONTINENTE</dd><dt>Valor:</dt><dd>2.060,00</dd><dt>Cond.:</dt><dd>330,00</dd><dt>IPTU:</dt><dd>87,89</dd></dl></article>

<footer class="footer">
  <h3 style="left:157px">MENU</h3>
  <ul style="left:157px"><li>A empresa</li><li>Localização</li><li>Área Restrita</li><li>Fale Conosco</li></ul>
  <ul style="left:271px"><li>Cadastre seu imóvel</li><li>Informações ao Proprietário</li><li>Informações ao Locatário</li><li>Solicite seu imóvel</li></ul>
  <h3 style="left:465px">CUSTOMERS</h3>
  <ul style="left:465px"><li>Privacy</li><li>Terms of use</li><li>Contact Support</li><li>FAQ</li></ul>
  <div class="vline"></div>
  <h3 style="left:619px">CONTACT</h3>
  <address class="address" style="font-style:normal"><strong>Lartovira</strong><br>Rua das Acácias, 140<br>Esquina com a Rua Lino Prado<br>Centro - Florianópolis</address>
  <div class="details"><span>CEP :</span><span>88010-400</span><span>Fax :</span><span>(48) 3200-1190</span><span>Locação :</span><span>(48) 3200-1191</span><span>Email :</span><a href="#">info@lartovira-exemplo.com.br</a></div>
</footer>
<div class="copyright">© (C) 2013 - Lartovira - Todos os direitos reservados.</div>
</body>
</html>
```